Thornvale Climate Business Card Design

Design new, 2 sides, business cards for a residential and light commercial heating, air conditioning contractor.

Target Market(s)

Homeowners, small businesses

Industry/Entity Type

Business

Contact Information for Business Card

Dominic Westerhall
Phone - 862-415-2736
Email
Address - PO box 518
Brightwater NJ 07912
Website - www.HarborBreezeLLC.example

Requirements
Must have
• logo, company colors, standard size with no die cut, so I can use nova stamp

```html
<!DOCTYPE html>
<html lang="en">
<head>
<meta charset="utf-8">
<title>Thornvale Climate Business Card</title>
<link rel="stylesheet" href="https://fonts.googleapis.com/css2?family=Arimo:wght@400;700&display=swap">
<style>
  :root {
    --maroon: #9b1f34;
    --orange: #f39a1e;
    --ink: #1a1a1a;
    --paper: #ffffff;
    --backdrop: #e6e4e1;
  }
  * { margin: 0; padding: 0; box-sizing: border-box; }
  html, body {
    width: 1200px;
    height: 950px;
    overflow: hidden;
    background: var(--backdrop);
    font-family: "Arimo", Arial, sans-serif;
  }
  .sheet {
    width: 1200px;
    height: 950px;
    display: flex;
    flex-direction: column;
    align-items: center;
    justify-content: center;
    gap: 50px;
  }
  .card {
    position: relative;
    width: 700px;
    height: 400px;
    background: var(--paper);
    overflow: hidden;
    box-shadow: 0 6px 18px rgba(0, 0, 0, 0.18);
  }
  .brand {
    position: absolute;
    display: flex;
    align-items: center;
    gap: 12px;
    color: var(--maroon);
    font-weight: 700;
    font-size: 30px;
    letter-spacing: 0.5px;
    white-space: nowrap;
  }
  .brand-dot {
    width: 22px;
    height: 22px;
    border-radius: 50%;
    background: var(--orange);
  }
  .card-back .brand { right: 50px; bottom: 60px; }
  .card-front .brand { left: 50px; top: 55px; font-size: 34px; }
  .front-band {
    position: absolute;
    inset: 0;
    width: 100%;
    height: 100%;
  }
  .holder {
    position: absolute;
    left: 420px;
    top: 150px;
    white-space: nowrap;
  }
  .holder-name {
    color: var(--maroon);
    font-weight: 700;
    font-size: 22px;
    letter-spacing: 0.5px;
  }
  .holder-title {
    color: var(--orange);
    font-size: 18px;
    margin-top: 4px;
    letter-spacing: 0.5px;
  }
  .contact {
    position: absolute;
    left: 40px;
    top: 255px;
    color: var(--paper);
    font-size: 15px;
    font-style: normal;
    line-height: 1.7;
    white-space: nowrap;
  }
</style>
</head>
<body>
<main class="sheet">
  <section class="card card-back" aria-label="Card back">
    <div class="brand"><span class="brand-dot"></span>Thornvale Climate</div>
  </section>

  <section class="card card-front" aria-label="Card front">
    <svg class="front-band" viewBox="0 0 700 400" preserveAspectRatio="none" aria-hidden="true">
      <path d="M0 170 C 200 190 450 280 700 330 L700 400 L0 400 Z" fill="var(--maroon)"/>
      <path d="M0 158 C 200 178 450 262 700 310 L700 330 C 450 280 200 190 0 170 Z" fill="var(--orange)"/>
      <path d="M0 155 C 200 175 450 258 700 306" fill="none" stroke="var(--ink)" stroke-width="2"/>
    </svg>
    <div class="brand"><span class="brand-dot"></span>Thornvale Climate</div>
    <div class="holder">
      <p class="holder-name">DOMINIC WESTERHALL</p>
      <p class="holder-title">PRESIDENT</p>
    </div>
    <address class="contact">
      <p>PO box 518, Brightwater NJ 07912</p>
      <p>P : 862 415 2736 &nbsp;M : 862 555 0148</p>
      <p>F : 862 555 0193 &nbsp;E : dominic@thornvaleclimate.example</p>
      <p>W : www.ThornvaleClimateLLC.example</p>
    </address>
  </section>
</main>
</body>
</html>
```